Business Card and Letterhead for Pimlu - modern real estate business

I need a double sided business card design for Pimlu. Please see business card brief here https://files.trelvonadocs.com/sheet/r/7QzTmWbaXLJnoPEd-kRyUgFhHsstbvCe2qfoMxDa_pz/view?mode=shared

Please feel free to design the business cards however you feel best. I am happy to give some creative freedoms and then provide feedback from there.

Please then also create a letterhead to match the business card design

Colors

Designer to choose colors to be used in the design.

Requirements
Must have
• Must be a modern, elegant business card which looks very professional

```html
<!DOCTYPE html>
<html lang="en">
<head>
<meta charset="utf-8">
<title>Pimlu Business Card</title>
<link rel="stylesheet" href="https://fonts.googleapis.com/css2?family=Roboto:wght@400;700&display=swap">
<style>
  :root {
    --stage: #3a3a3c;
    --card-black: #1b1b1c;
    --band-black: #0c0c0c;
    --paper: #ffffff;
    --brand-red: #e30613;
    --photo-top: #e9e9ea;
    --photo-bottom: #4a4d52;
    --ink-light: #f2f2f2;
  }
  * { box-sizing: border-box; margin: 0; padding: 0; }
  html, body {
    width: 1200px; height: 960px; overflow: hidden;
    background: var(--stage);
    font-family: "Roboto", Arial, sans-serif;
  }
  .canvas {
    position: relative; width: 1200px; height: 960px;
  }
  .card {
    position: absolute; left: 250px; width: 700px; height: 400px;
    overflow: hidden;
  }
  .card--back { top: 50px; background: var(--card-black); }
  .card--front { top: 510px; background: var(--paper); }

  .wordmark {
    position: absolute;
    font-weight: 700; color: var(--brand-red);
    letter-spacing: 4px; line-height: 1;
  }
  .card--back .wordmark {
    font-size: 84px; left: 0; right: 0; top: 158px; text-align: center;
  }
  .card--front .wordmark {
    font-size: 64px; left: 56px; top: 120px;
  }

  .portrait {
    position: absolute; right: 0; top: 0; width: 330px; height: 300px;
    background: linear-gradient(180deg, var(--photo-top) 0%, #c9c9cb 40%, var(--photo-bottom) 100%);
  }

  .name-tab {
    position: absolute; left: 0; top: 248px; width: 360px; height: 52px;
  }
  .name-tab svg { display: block; }
  .name-tab__text {
    position: absolute; left: 28px; top: 6px; color: var(--paper);
  }
  .agent-name { font-size: 20px; font-weight: 700; line-height: 22px; }
  .agent-role { font-size: 14px; font-weight: 400; line-height: 18px; }

  .contact-band {
    position: absolute; left: 0; right: 0; bottom: 0; height: 100px;
    background: var(--band-black); color: var(--ink-light);
    font-size: 14px; line-height: 22px;
    padding: 24px 28px 0;
  }
  .contact-band .web {
    position: absolute; right: 28px; top: 24px;
  }
</style>
</head>
<body>
<main class="canvas">
  <section class="card card--back" aria-label="Card back">
    <div class="wordmark">PIMLU</div>
  </section>

  <section class="card card--front" aria-label="Card front">
    <div class="wordmark">PIMLU</div>

    <div class="portrait" role="img" aria-label="Portrait photo of the agent in a dark suit"></div>

    <div class="name-tab">
      <svg width="360" height="52" viewBox="0 0 360 52" aria-hidden="true">
        <polygon points="0,52 0,22 250,22 270,0 300,0 360,52" fill="var(--brand-red)"/>
        <polygon points="0,52 0,10 250,10 262,0 300,0 360,52" fill="var(--brand-red)"/>
      </svg>
      <div class="name-tab__text">
        <p class="agent-name">Dane Mercer</p>
        <p class="agent-role">Licenced Real Estate Agent</p>
      </div>
    </div>

    <div class="contact-band">
      <p class="address">PO Box 1182, Brellton NSW 2690</p>
      <p class="lines">P. 0412 555 309 &nbsp; E. dane@pimlu.com</p>
      <p class="web">W. www.pimlu.com</p>
    </div>
  </section>
</main>
</body>
</html>
```